Calvanto Group Real Estate Company business cards

New business card design, we are generally happy with the basic layout of the existing front of business card, (feel free to change) but require a head shot photo on the back side.

http://www.calvanto.com.au/

Attached logos, and existing business card

------------------------------

Target Market(s)

Real estate

Industry/Entity Type

Real Estate

Contact Information for Business Card

Standard size double sided

Font styles to use
Other font styles liked:
• Futura

Requirements
Must have
• Photo head shot on the back side
Nice to have
• yes
Should not have
• No

```html
<!DOCTYPE html>
<html lang="en">
<head>
<meta charset="utf-8">
<title>Calvanto Group – Business Cards</title>
<link href="https://fonts.googleapis.com/css2?family=Jost:wght@400;500&family=Arimo:wght@400&display=swap" rel="stylesheet">
<style>
  :root {
    --bg: #ecebe8;
    --purple: #2b1f5c;
    --orange: #e38a2b;
    --white: #ffffff;
    --grey-text: #8c86a3;
    --rule: #6d6491;
    --photo-light: #e9e9ea;
    --photo-mid: #c9c9cc;
  }
  html, body {
    margin: 0;
    width: 1200px;
    height: 892px;
    overflow: hidden;
    background: var(--bg);
  }
  .canvas {
    position: relative;
    width: 1200px;
    height: 892px;
    display: flex;
    align-items: center;
    justify-content: center;
    gap: 40px;
  }
  .card {
    position: relative;
    width: 540px;
    height: 309px;
    overflow: hidden;
    box-shadow: 0 6px 18px rgba(0,0,0,0.18);
  }
  /* Front */
  .card-front { background: var(--purple); color: var(--white); }
  .front-brand {
    position: absolute;
    left: 34px;
    top: 168px;
    font-family: "Jost", sans-serif;
    font-weight: 400;
    font-size: 38px;
    letter-spacing: -0.5px;
    color: var(--white);
  }
  .divider {
    position: absolute;
    left: 282px;
    top: 40px;
    width: 1px;
    height: 228px;
    background: var(--rule);
  }
  .contact {
    position: absolute;
    left: 304px;
    top: 44px;
    font-family: "Arimo", sans-serif;
  }
  .contact-name {
    font-size: 23px;
    color: var(--orange);
    margin: 0;
    line-height: 1.1;
  }
  .contact-title {
    font-size: 15px;
    margin: 2px 0 26px;
  }
  .contact-line {
    display: flex;
    align-items: center;
    gap: 8px;
    font-size: 14px;
    line-height: 22px;
  }
  .contact-line.abn { padding-left: 0; }
  .icon { width: 12px; height: 12px; flex: none; }
  /* Back */
  .card-back { background: var(--white); }
  .headshot-area {
    position: absolute;
    inset: 0;
  }
  .back-brand {
    position: absolute;
    left: 150px;
    top: 208px;
    font-family: "Jost", sans-serif;
    font-weight: 400;
    font-size: 40px;
    letter-spacing: -0.5px;
    color: var(--purple);
  }
</style>
</head>
<body>
<main class="canvas">
  <section class="card card-front" aria-label="Business card front">
    <div class="front-brand">calvanto group</div>
    <div class="divider"></div>
    <div class="contact">
      <h1 class="contact-name">Daniel Tran</h1>
      <div class="contact-title">Director</div>
      <div class="contact-line abn">ABN: 51 204 683 917</div>
      <div class="contact-line">
        <svg class="icon" viewBox="0 0 12 12"><rect width="12" height="12" fill="var(--orange)"/><path d="M3.5 2.5h2l.6 2-1.1.7a5 5 0 0 0 2 2l.7-1.1 2 .6v2a1 1 0 0 1-1 1A6.5 6.5 0 0 1 2.5 3.5a1 1 0 0 1 1-1z" fill="var(--purple)"/></svg>
        0412 508 316
      </div>
      <div class="contact-line">
        <svg class="icon" viewBox="0 0 12 12"><rect width="12" height="12" fill="var(--orange)"/><circle cx="6" cy="6" r="3.3" fill="none" stroke="var(--purple)" stroke-width="1"/><path d="M2.7 6h6.6M6 2.7v6.6" stroke="var(--purple)" stroke-width="0.8"/></svg>
        www.calvanto.com.au
      </div>
      <div class="contact-line">
        <svg class="icon" viewBox="0 0 12 12"><rect width="12" height="12" fill="var(--orange)"/><rect x="2.5" y="3.5" width="7" height="5" fill="none" stroke="var(--purple)" stroke-width="1"/><path d="M2.5 3.5 6 6.3l3.5-2.8" fill="none" stroke="var(--purple)" stroke-width="1"/></svg>
        daniel.tran@calvanto.com.au
      </div>
    </div>
  </section>

  <section class="card card-back" aria-label="Business card back">
    <svg class="headshot-area" viewBox="0 0 540 309" preserveAspectRatio="none">
      <defs>
        <linearGradient id="photoTone" x1="0" y1="0" x2="1" y2="1">
          <stop offset="0" stop-color="var(--photo-light)"/>
          <stop offset="1" stop-color="var(--photo-mid)"/>
        </linearGradient>
      </defs>
      <path role="img" aria-label="Head shot photo of the director" d="M0 0H540V0L540 0V0H540 0Z M0 0H330C320 60 300 120 260 170 220 220 120 260 0 270Z" fill="url(#photoTone)"/>
      <path d="M330 0C320 60 300 120 260 170 220 220 120 260 0 270V278C130 266 230 228 272 174 312 122 330 62 340 0Z" fill="var(--orange)"/>
    </svg>
    <div class="back-brand" style="left:300px;top:230px;">calvanto group</div>
  </section>
</main>
</body>
</html>
```